sydney wedding photography business needs a business card design

we need a business card design for a sydney based wedding photography and videography business. our business name is :golden hour studio and film. our target clients are 24-35 yrs female. our style is candid, organic, natural, dynamic. we are a team of young photographers and videographers, and help brides to create memories that they will cherish for the rest of their lives. the logo will be provided. we want an elegant design that reflects our style, and also want to give a great impression to our clients that we are one of the best studios in sydney and our brand means quality and premium service.

Target Market(s)

bride to be, 24-35 years old, living in sydney and surrunding areas

Industry/Entity Type

Wedding Photography

Contact Information for Business Card

address: 57 tarrant street, glenmore nsw 2047
mobile: 0431872259
phone: (02) 9163 2408
info@tidewillowstudio.net.au
www.tidewillowstudio.net.au
facebook:tidewillowweddings
instagram:tidewillowweddings

Font styles to use
Serif
Sans Serif

Requirements
Nice to have
• maybe add my slogan"memories beyond eternity" if the layout looks good
Should not have
• no black color, not good idea for wedding biz card

```html
<!DOCTYPE html>
<html lang="en">
<head>
<meta charset="utf-8">
<title>Golden Hour Studio and Film – Business Card</title>
<link rel="stylesheet" href="https://fonts.googleapis.com/css2?family=Josefin+Sans:wght@300;400;600&display=swap">
<style>
  :root {
    --bg: #ece7dd;
    --gold-light: #e0b02c;
    --gold: #cf9c1c;
    --gold-deep: #a97c0e;
    --espresso: #3a2511;
    --text-dark: #2e1d0b;
    --logo-gold: #e9b732;
  }
  * { box-sizing: border-box; margin: 0; padding: 0; }
  html, body {
    width: 1200px; height: 950px; overflow: hidden;
    background: var(--bg);
    font-family: "Josefin Sans", "Century Gothic", sans-serif;
  }
  .stage {
    width: 1200px; height: 950px;
    display: flex; flex-direction: column; align-items: center; justify-content: center;
    gap: 30px;
  }
  .card {
    position: relative;
    width: 760px; height: 434px;
    overflow: hidden;
    background: linear-gradient(135deg, var(--gold-light) 0%, var(--gold) 55%, var(--gold-deep) 100%);
    box-shadow: 0 8px 22px rgba(0,0,0,.18);
  }
  .card-front__shape { position: absolute; inset: 0; width: 100%; height: 100%; }
  .card-front__field, .card-front__stripe { fill: var(--espresso); }
  .brand {
    position: absolute; right: 70px; top: 62px;
    color: var(--logo-gold);
    font-weight: 400; font-size: 30px; letter-spacing: 1px;
    display: flex; align-items: center; gap: 12px;
  }
  .brand__dot {
    width: 12px; height: 12px; border-radius: 50%;
    background: var(--logo-gold);
  }
  .contact {
    position: absolute; left: 48px; top: 186px;
    color: var(--text-dark);
  }
  .contact__name {
    font-weight: 300; font-size: 27px; letter-spacing: 1px;
    text-transform: uppercase; line-height: 1;
  }
  .contact__role {
    font-weight: 400; font-size: 13px; letter-spacing: 1.5px;
    text-transform: uppercase; margin-top: 4px;
  }
  .contact__address {
    font-weight: 300; font-size: 15px; line-height: 19px; margin-top: 12px;
  }
  .contact__list { list-style: none; margin-top: 10px; }
  .contact__item {
    display: flex; align-items: center; gap: 10px;
    font-weight: 300; font-size: 15px; line-height: 21px;
  }
  .contact__icon {
    width: 14px; height: 14px; flex: none;
    background: var(--text-dark); border-radius: 2px;
    display: flex; align-items: center; justify-content: center;
  }
  .contact__icon svg { width: 10px; height: 10px; }
  .contact__icon--round { border-radius: 50%; }
</style>
</head>
<body>
<main class="stage">
  <section class="card card-front">
    <svg class="card-front__shape" viewBox="0 0 760 434" preserveAspectRatio="none" aria-hidden="true">
      <path class="card-front__field" d="M0 0 H760 V230 C560 220 360 160 200 100 C130 76 60 66 0 66 Z"/>
      <path class="card-front__stripe" d="M0 80 C60 80 130 90 200 114 C360 174 560 238 720 252 C560 252 360 200 200 130 C130 104 60 94 0 94 Z"/>
    </svg>
    <div class="brand">golden hour studio and film<span class="brand__dot"></span></div>
    <div class="contact">
      <p class="contact__name">Mara Ellison</p>
      <p class="contact__role">Photographer</p>
      <p class="contact__address">57 tarrant street<br>glenmore nsw 2047</p>
      <ul class="contact__list">
        <li class="contact__item"><span class="contact__icon"><svg viewBox="0 0 10 10"><path d="M2 1 L4 1 L4.6 3 L3.6 3.8 C4.2 5 5 5.8 6.2 6.4 L7 5.4 L9 6 L9 8 C9 8.6 8.6 9 8 9 C4.2 9 1 5.8 1 2 C1 1.4 1.4 1 2 1 Z" fill="#cf9c1c"/></svg></span>(02) 9163 2408</li>
        <li class="contact__item"><span class="contact__icon"><svg viewBox="0 0 10 10"><rect x="3" y="1" width="4" height="8" rx="0.8" fill="none" stroke="#cf9c1c" stroke-width="1"/></svg></span>0431 872 259</li>
        <li class="contact__item"><span class="contact__icon"><svg viewBox="0 0 10 10"><rect x="1" y="2.5" width="8" height="5" fill="none" stroke="#cf9c1c" stroke-width="1"/><path d="M1 2.5 L5 5.5 L9 2.5" fill="none" stroke="#cf9c1c" stroke-width="1"/></svg></span>info@tidewillowstudio.net.au</li>
        <li class="contact__item"><span class="contact__icon contact__icon--round"><svg viewBox="0 0 10 10"><circle cx="5" cy="5" r="3.5" fill="none" stroke="#cf9c1c" stroke-width="1"/><path d="M1.5 5 H8.5 M5 1.5 C3.5 3.5 3.5 6.5 5 8.5 C6.5 6.5 6.5 3.5 5 1.5" fill="none" stroke="#cf9c1c" stroke-width="0.8"/></svg></span>www.tidewillowstudio.net.au</li>
        <li class="contact__item"><span class="contact__icon"></span>tidewillowweddings</li>
        <li class="contact__item"><span class="contact__icon contact__icon--round"></span>tidewillowweddings</li>
      </ul>
    </div>
  </section>
  <section class="card card-back" aria-label="Card back"></section>
</main>
</body>
</html>
```